Law Firm in Texas in need of new letterhead

Law Firm in Fort Worth, TX, USA named "Pell & Varnum, Attorneys-At-Law, LLP." This is a general practice law firm that mostly does Family Law and Criminal Defense work.

We are looking for a new letterhead that has a "classical" appeal, with modern elements.

Any color combination is fine, but please note that we do fax many documents, so the design must be clearly legible in Black and White.

We would like our letterhead to project a sense of professionalism, integrity, and ability.

Target Market(s)

Letterhead will be for correspondence generally with other attorneys and clients.

Industry/Entity Type

Law Firm

Logo Text

Pell & Varnum, Attorneys-At-Law, LLP.

Logo styles of interest
Pictorial/Combination Logo
Wordmark Logo
Lettermark Logo
Requirements
Nice to have
• Although not necessary, a "Texas Star" that is incorporated into the design would be a nice touch.
Should not have
• Colors that do not convert to B&W easily

```html
<!DOCTYPE html>
<html lang="en">
<head>
<meta charset="utf-8">
<title>Pell &amp; Varnum Letterhead</title>
<link href="https://fonts.googleapis.com/css2?family=Cinzel:wght@400;500&family=Questrial&display=swap" rel="stylesheet">
<style>
  :root {
    --backdrop: #e4e5e7;
    --paper: #ffffff;
    --navy: #2b4f7e;
    --ink: #3a3a3a;
    --muted: #8a8a8a;
    --rule: #b9bec6;
  }
  * { box-sizing: border-box; margin: 0; padding: 0; }
  html, body { width: 1200px; height: 1000px; overflow: hidden; }
  body {
    background: var(--backdrop);
    font-family: "Questrial", "Century Gothic", sans-serif;
    color: var(--ink);
    position: relative;
  }
  .letterhead {
    position: absolute;
    left: 237px; top: 30px;
    width: 726px; height: 940px;
    background: var(--paper);
    box-shadow: 0 4px 18px rgba(0,0,0,0.12);
    padding: 64px 62px 56px 66px;
  }
  .brand { display: flex; align-items: center; gap: 14px; }
  .brand-square { width: 46px; height: 46px; background: var(--navy); flex: none; }
  .brand-text { color: var(--navy); font-family: "Cinzel", serif; }
  .brand-name { font-size: 27px; font-weight: 500; letter-spacing: 1.5px; line-height: 1; }
  .brand-tagline {
    display: flex; align-items: center; gap: 8px;
    font-size: 12.5px; letter-spacing: 1.2px; margin-top: 6px;
  }
  .brand-tagline::before, .brand-tagline::after {
    content: ""; width: 22px; height: 1px; background: var(--navy);
  }
  .content { position: absolute; left: 66px; right: 62px; top: 250px; display: flex; gap: 26px; }
  .body-copy { flex: 1; font-size: 11.5px; line-height: 1.55; color: var(--ink); text-align: justify; }
  .body-copy p { margin-bottom: 14px; }
  .partners {
    width: 160px; flex: none; text-align: right;
    border-right: 1px solid var(--rule); padding-right: 10px;
    font-size: 9.5px; line-height: 1.45; color: var(--muted);
    align-self: flex-start;
  }
  .partner-name { font-weight: bold; color: #6a6a6a; letter-spacing: 0.5px; font-size: 10px; }
  .partner + .partner { margin-top: 10px; }
  .role { margin-bottom: 8px; }
  .closing { position: absolute; left: 66px; top: 720px; display: flex; align-items: center; gap: 50px; }
  .closing-words { font-size: 12px; }
  .signer { font-size: 15px; font-weight: bold; color: #222; margin-top: 16px; }
  .signature { width: 150px; height: 56px; background: linear-gradient(90deg, #dfe6f1, #eef2f8); border-radius: 6px; }
  .contact {
    position: absolute; left: 66px; bottom: 56px;
    display: flex; gap: 12px; font-size: 11px; line-height: 1.45; color: var(--navy);
  }
  .contact-address { padding-right: 12px; border-right: 1px solid var(--navy); }
  .contact-label { font-weight: bold; }
</style>
</head>
<body>
  <main class="letterhead">
    <header class="brand">
      <div class="brand-square"></div>
      <div class="brand-text">
        <div class="brand-name">Pell &amp; Varnum</div>
        <div class="brand-tagline">Attorneys At Law, LLP</div>
      </div>
    </header>

    <section class="content">
      <div class="body-copy">
        <p>Lorem ipsum dolor sit amet, consectetur adipiscing elit, sed do eiusmod tempor incididunt ut labore et dolore magna aliqua. Ut enim ad minim veniam, quis nostrud exercitation ullamco laboris nisi ut aliquip ex ea commodo consequat. Duis aute irure dolor in reprehenderit in voluptate velit esse cillum dolore eu fugiat nulla pariatur. Excepteur sint occaecat cupidatat non proident, sunt in culpa qui officia deserunt mollit anim id est laborum.</p>
        <p>Sed do eiusmod tempor incididunt ut labore et dolore magna aliqua. Ut enim ad minim veniam, quis nostrud exercitation ullamco laboris nisi ut aliquip ex ea commodo. Duis aute irure dolor in reprehenderit in voluptate velit esse cillum dolore eu fugiat nulla pariatur, sunt in culpa qui officia deserunt mollit anim id est laborum.</p>
        <p>Lorem ipsum dolor sit amet, consectetur adipiscing elit, sed do eiusmod tempor incididunt ut labore et dolore magna aliqua. Quis nostrud exercitation ullamco laboris nisi ut aliquip ex ea commodo consequat, excepteur sint occaecat cupidatat non proident.</p>
        <p>Ut enim ad minim veniam, quis nostrud exercitation ullamco laboris nisi ut aliquip ex ea commodo consequat. Duis aute irure dolor in reprehenderit in voluptate velit esse cillum dolore eu fugiat nulla pariatur. Excepteur sint occaecat cupidatat non proident, sunt in culpa qui officia deserunt mollit anim id est laborum.</p>
      </div>
      <aside class="partners">
        <div class="partner">
          <div class="partner-name">ADRIAN PELL</div>
          <div class="role">Managing Partner</div>
          <div>- Licensed in State of Texas</div>
          <div>- United States District Court</div>
          <div>- United States Supreme Court</div>
        </div>
        <div class="partner">
          <div class="partner-name">CLAIRE MARIE VARNUM</div>
          <div>- Licensed in the State of Texas</div>
        </div>
      </aside>
    </section>

    <section class="closing">
      <div>
        <div class="closing-words">Yours Sincerely,</div>
        <div class="signer">Mara Ellison</div>
      </div>
      <div class="signature" role="img" aria-label="Handwritten signature in blue ink"></div>
    </section>

    <footer class="contact">
      <div class="contact-address">1420 E. Harlow St.<br>Fort Worth, TX 76104</div>
      <div><span class="contact-label">Phone:</span> (817) 555-0142<br><span class="contact-label">Fax:</span> (817) 555-0187</div>
    </footer>
  </main>
</body>
</html>
```